TREVAL BUILDWORKS, LLC Webpage portfolio

I want to create a Website that allows my potential clients to browse my Skilled work via before and after photos. I want the website to enhance the work that I provide and potentially drive new business, or at least solidify my work.
I also do 3D CAD and Modeling of New Spaces and it would be nice to show some of that work from pencil design to 3D modeling, which I feel may help give me more clients.

The website needs to show a solid carpenter/company with the skills to get any project completed.

Types of Jobs - Custom Carpentry & Finishes, Kitchens, Baths, Basements, Decks, Porches, Whole House Renovation - Skilled Craftsmanship (Hardwood Flooring, Floor and Wall Tile) and much more...

Target Market(s)

Residential Home Renovation, Kitchen and Bath Renovation, Home Improvement

Industry/Entity Type

Residential Construction

Number of Pages Required

5+ page

Font styles to use
Sans Serif
Script

Requirements
Must have
• Similar to Plinvo.com, except for Treval Buildworks.
• Must be inviting.
• My Services Offered
• A way to reach me or contact me for estimates with some sort of Screening Questionare.
Nice to have
• Inviting Colors
Should not have
• Not sure at this time

```html
<!DOCTYPE html>
<html lang="en">
<head>
<meta charset="utf-8">
<title>Treval Buildworks — Finished Carpentry</title>
<link rel="stylesheet" href="https://fonts.googleapis.com/css2?family=Didact+Gothic&display=swap">
<style>
  :root {
    --bg-dark: #2a1b12;
    --bg-mid: #6b3f22;
    --bg-warm: #a8652f;
    --header: rgba(44, 30, 22, 0.94);
    --pill: rgba(18, 11, 7, 0.62);
    --panel: rgba(22, 14, 9, 0.5);
    --text: #f4efe8;
    --muted: #d9d2c8;
  }
  * { margin: 0; padding: 0; box-sizing: border-box; }
  html, body { width: 1200px; height: 800px; overflow: hidden; }
  body {
    font-family: "Didact Gothic", "Helvetica Neue", Arial, sans-serif;
    color: var(--text);
    position: relative;
    background: var(--bg-dark);
  }
  .hero-photo {
    position: absolute; inset: 0;
    background:
      radial-gradient(ellipse at 55% 40%, rgba(190,120,60,0.55), transparent 60%),
      linear-gradient(180deg, #3a2517 0%, var(--bg-mid) 45%, #7a4a2a 70%, #4a3226 100%);
  }
  .site-header {
    position: absolute; top: 0; left: 0; width: 1200px; height: 100px;
    background: var(--header);
  }
  .brand {
    position: absolute; left: 30px; top: 50px;
    display: flex; align-items: center; gap: 6px;
    font-size: 13px; color: var(--muted);
  }
  .brand-mark { width: 10px; height: 10px; background: var(--muted); }
  .social { position: absolute; left: 292px; top: 66px; display: flex; gap: 12px; }
  .social span { width: 14px; height: 14px; border-radius: 50%; background: var(--text); display: block; }
  .main-nav {
    position: absolute; right: 28px; top: 66px;
    display: flex; gap: 31px;
    font-size: 13px; letter-spacing: 2.6px;
  }
  .slide-title {
    position: absolute; right: 27px; top: 194px;
    font-size: 35px; letter-spacing: 6.5px; font-weight: 400;
  }
  .slider-controls {
    position: absolute; left: 850px; top: 274px; width: 130px; height: 49px;
    border-radius: 25px; background: var(--pill);
  }
  .slider-controls svg { position: absolute; top: 17px; }
  .action-btn {
    position: absolute; left: 30px; width: 370px; height: 50px;
    border-radius: 25px; background: var(--pill);
    display: flex; align-items: center; justify-content: center;
    font-size: 17px; letter-spacing: 3.4px;
  }
  .btn-feedback { top: 350px; }
  .btn-estimate { top: 425px; }
  .services {
    position: absolute; left: 850px; top: 350px; width: 350px; height: 450px;
    background: var(--panel); text-align: right; padding-right: 30px;
  }
  .services h2 {
    font-weight: 400; font-size: 24px; letter-spacing: 4.4px;
    margin-top: 47px; margin-right: -2px;
  }
  .services p { font-size: 11px; line-height: 14.5px; text-transform: uppercase; }
  .services .list-top { margin-top: 57px; }
  .services .list-rooms { margin-top: 15px; }
  .services h3 { font-weight: 400; font-size: 16px; margin-top: 36px; }
  .services .craft { margin-top: 16px; padding-left: 60px; }
  .services .more { margin-top: 14px; }
</style>
</head>
<body>
  <div class="hero-photo" role="img" aria-label="Warm-lit kitchen with dark wood cabinets, pendant lights and tiled backsplash"></div>

  <header class="site-header">
    <div class="brand"><span class="brand-mark"></span>Treval Buildworks</div>
    <div class="social" aria-label="Social links"><span></span><span></span><span></span><span></span></div>
    <nav class="main-nav">
      <span>KITCHENS</span><span>BATHS</span><span>BASEMENTS</span><span>FINISHED CARPENTRY</span><span>DECKS &amp; PORCHES</span>
    </nav>
  </header>

  <h1 class="slide-title">FINISHED CARPENTRY</h1>
  <div class="slider-controls">
    <svg style="left:20px" width="10" height="16" viewBox="0 0 10 16"><path d="M9 0 L0 8 L9 16 Z" fill="#fff"/></svg>
    <svg style="left:102px" width="10" height="16" viewBox="0 0 10 16"><path d="M1 0 L10 8 L1 16 Z" fill="#fff"/></svg>
  </div>

  <a class="action-btn btn-feedback">CLIENTS FEEDBACK</a>
  <a class="action-btn btn-estimate">REQUEST AN&nbsp; ESTIMATE</a>

  <section class="services">
    <h2>MY SERVICES</h2>
    <p class="list-top">3D CAD modelling of new spaces<br>custom<br>carpentry &amp; finishes,</p>
    <p class="list-rooms">kitchens,<br>baths,<br>basements,<br>decks,<br>porches,</p>
    <h3>WHOLE HOUSE RENOVATION</h3>
    <p class="craft">skilled craftsmanship ((hardwood flooring, floor and wall tile)</p>
    <p class="more">and much more</p>
  </section>
</body>
</html>
```